Equine Podcast Cover Art Design

We need catchy cover art for a horse related podcast "Ride Onward Together"
Brief show description"
Whether you want to ride to experience horses, develop yourself to the next level as a horseman/horsewoman or ride to improve your physical and mental health, we are committed to helping you Ride Onward TogetherĀ®. Join us as we explore the nuance of equine management and sports as well as interview industry professionals to provide you with the knowledge necessary to be a better partner for your equine friends.
I have uploaded two existing logos we use for various purposes to give you an idea of existing style.
Target Market(s)
Horse owners and other equine professionals
Look and feel
Each slider illustrates characteristics of the customer's brand and the style your logo design should communicate.

```html
<!DOCTYPE html>
<html lang="en">
<head>
<meta charset="utf-8">
<title>Ride Onward Together – Podcast Cover</title>
<link href="https://fonts.googleapis.com/css2?family=Bebas+Neue&display=swap" rel="stylesheet">
<style>
  :root {
    --bg-deep: #1a0b08;
    --bg-mid: #3a1a12;
    --bg-warm: #7a3320;
    --cream: #efe0c2;
    --tan: #d8ab88;
    --white: #ffffff;
    --photo-dark: #2a1510;
    --photo-bay: #8a4a26;
  }
  * { margin: 0; padding: 0; box-sizing: border-box; }
  html, body { width: 1200px; height: 1200px; overflow: hidden; background: var(--bg-deep); }
  .cover {
    position: relative;
    width: 1200px;
    height: 1200px;
    overflow: hidden;
    font-family: "Bebas Neue", "Oswald", sans-serif;
  }
  .arena-backdrop {
    position: absolute;
    inset: 0;
    background:
      radial-gradient(ellipse 60% 45% at 72% 48%, var(--bg-warm) 0%, rgba(122,51,32,0.35) 45%, rgba(0,0,0,0) 75%),
      linear-gradient(180deg, var(--bg-mid) 0%, #2a130d 55%, var(--bg-deep) 100%);
  }
  .brand-mark {
    position: absolute;
    left: 101px;
    top: 90px;
    width: 218px;
    height: 218px;
    display: flex;
    align-items: center;
    justify-content: center;
  }
  .brand-mark .ring {
    position: absolute;
    inset: 0;
    border: 4px solid var(--white);
    border-radius: 50%;
  }
  .brand-mark .brand-name {
    color: var(--white);
    font-size: 34px;
    line-height: 1;
    text-align: center;
    letter-spacing: 1px;
  }
  .rider-photo {
    position: absolute;
    left: 547px;
    top: 55px;
    width: 653px;
    height: 775px;
    border-radius: 40% 8% 10% 45% / 30% 6% 20% 40%;
    background: radial-gradient(ellipse at 45% 55%, var(--photo-bay) 0%, #5a2c17 50%, var(--photo-dark) 100%);
  }
  .title {
    position: absolute;
    left: 98px;
    top: 0;
    color: var(--cream);
    line-height: 1;
  }
  .title .line {
    position: absolute;
    left: 0;
    white-space: nowrap;
    font-size: 212px;
    line-height: 1;
  }
  .title .ride { top: 378px; }
  .title .onward { top: 544px; }
  .title .together {
    top: 790px;
    left: 6px;
    font-size: 292px;
    color: var(--tan);
  }
  .registered {
    position: absolute;
    left: 1078px;
    top: 822px;
    width: 34px;
    height: 34px;
    border: 2px solid var(--white);
    border-radius: 50%;
    color: var(--white);
    font-family: Arial, sans-serif;
    font-size: 18px;
    line-height: 30px;
    text-align: center;
  }
</style>
</head>
<body>
  <main class="cover">
    <div class="arena-backdrop" role="img" aria-label="Dimly lit indoor riding arena with warm light"></div>

    <div class="brand-mark">
      <span class="ring"></span>
      <span class="brand-name">Old Meadow<br>Farm</span>
    </div>

    <div class="rider-photo" role="img" aria-label="Bay horse jumping with a rider in navy jacket and black helmet"></div>

    <h1 class="title">
      <span class="line ride">RIDE</span>
      <span class="line onward">ONWARD</span>
      <span class="line together">TOGETHER</span>
    </h1>
    <span class="registered">R</span>
  </main>
</body>
</html>
```